Local Roofing/Construction company business needs new biz card design

We need a new business card design, current cards are from the start of this operation and generic at best. We are a local Construction Company (General Contractor) with a majority of our work originating from insurance claims-exterior finish work is the main focus (Roofs-Siding-Gutters etc). Heavily involved with homeowners and the low ball offers they receive from insurance company's after a insurable event takes place. I have attached some of our original logo file(s) below.

```html
<!DOCTYPE html>
<html lang="en">
<head>
<meta charset="utf-8">
<title>Ridgeline Construction – Business Card</title>
<link href="https://fonts.googleapis.com/css2?family=Open+Sans:wght@400;600;700;800&display=swap" rel="stylesheet">
<style>
  :root {
    --bg: #222222;
    --ink: #061c20;
    --green: #3fb45f;
    --green-deep: #2e9a4c;
    --paper: #f4f4f4;
    --white: #f2f0ee;
  }
  * { box-sizing: border-box; margin: 0; padding: 0; }
  html, body { width: 1200px; height: 780px; overflow: hidden; background: var(--bg); }
  body { font-family: "Open Sans", Arial, sans-serif; position: relative; }

  .card {
    position: absolute;
    width: 525px;
    height: 300px;
    top: 240px;
    border-radius: 3px;
    overflow: hidden;
    box-shadow: 0 12px 30px rgba(0,0,0,.45);
  }
  .card-front { left: 50px; background: var(--paper); }
  .card-back { left: 625px; }

  .front-shapes { position: absolute; inset: 0; width: 100%; height: 100%; }

  .brand-tab {
    position: absolute; left: 18px; top: 16px;
    background: var(--ink); border-radius: 10px;
    padding: 9px 16px 9px 12px;
    display: flex; align-items: center; gap: 9px;
  }
  .brand-square { width: 20px; height: 20px; background: var(--green); border-radius: 3px; }
  .brand-name {
    color: var(--white); font-weight: 800; font-size: 17px;
    letter-spacing: .04em; text-transform: uppercase; line-height: 1;
  }

  .contact { position: absolute; left: 22px; top: 84px; color: var(--ink); }
  .person {
    border-left: 6px solid var(--green); padding-left: 8px; margin-left: -22px; padding-left: 16px;
  }
  .person-name { font-size: 22px; font-weight: 700; line-height: 1.1; }
  .person-first { color: var(--green); }
  .person-role { font-size: 11px; margin-top: 2px; }
  .address { font-size: 11px; line-height: 1.4; margin-top: 10px; }
  .lines { list-style: none; margin-top: 8px; font-size: 11px; line-height: 1.55; }
  .lines li { display: flex; align-items: center; gap: 6px; }
  .icon { width: 11px; height: 11px; flex: none; }

  .feature-name {
    position: absolute; left: 310px; top: 118px; width: 190px;
    display: flex; flex-direction: column; align-items: center; gap: 10px;
  }
  .feature-square { width: 44px; height: 44px; background: var(--white); border-radius: 6px; }
  .feature-text {
    color: var(--white); font-weight: 800; font-size: 20px; text-align: center;
    letter-spacing: .04em; text-transform: uppercase; line-height: 1.15;
  }

  .back-pattern { position: absolute; inset: 0; background: var(--green); }
  .back-mark {
    position: absolute; right: 22px; bottom: 22px;
    display: flex; align-items: center; gap: 6px;
  }
  .back-square { width: 14px; height: 14px; border: 2px solid var(--white); border-radius: 3px; }
  .back-name {
    color: var(--white); font-weight: 800; font-size: 11px;
    letter-spacing: .04em; text-transform: uppercase;
  }
</style>
</head>
<body>

<section class="card card-front">
  <svg class="front-shapes" viewBox="0 0 525 300" preserveAspectRatio="none" aria-hidden="true">
    <path d="M400 0 C330 40 270 110 250 180 C285 100 345 40 430 0 Z" fill="var(--green)"/>
    <path d="M440 0 H525 V300 H232 C250 170 320 60 440 0 Z" fill="var(--ink)"/>
  </svg>

  <div class="brand-tab">
    <span class="brand-square"></span>
    <span class="brand-name">Ridgeline Construction</span>
  </div>

  <div class="contact">
    <div class="person">
      <p class="person-name"><span class="person-first">Marta</span> Kolarova</p>
      <p class="person-role">Co-Founder</p>
    </div>
    <p class="address">48 Cedar Hollow Ln,<br>Oakridge, MO 63999</p>
    <ul class="lines">
      <li>
        <svg class="icon" viewBox="0 0 12 12"><circle cx="6" cy="6" r="6" fill="var(--green)"/><path d="M4 3.2l1 1.3-.6.8c.4.9 1 1.5 1.9 1.9l.8-.6 1.3 1-.6 1c-2.4-.3-4.2-2.1-4.5-4.5z" fill="#fff"/></svg>
        555-204-3187
      </li>
      <li>
        <svg class="icon" viewBox="0 0 12 12"><circle cx="6" cy="6" r="6" fill="var(--green)"/><path d="M4 3.2l1 1.3-.6.8c.4.9 1 1.5 1.9 1.9l.8-.6 1.3 1-.6 1c-2.4-.3-4.2-2.1-4.5-4.5z" fill="#fff"/></svg>
        555-731-9046 (Emergency)
      </li>
      <li>
        <svg class="icon" viewBox="0 0 12 12"><circle cx="6" cy="6" r="6" fill="var(--green)"/><circle cx="6" cy="6" r="3.2" fill="none" stroke="#fff" stroke-width=".9"/><path d="M2.8 6h6.4M6 2.8c-1.3 1.8-1.3 4.6 0 6.4M6 2.8c1.3 1.8 1.3 4.6 0 6.4" fill="none" stroke="#fff" stroke-width=".7"/></svg>
        www.ridgelinebuild.com
      </li>
      <li>
        <svg class="icon" viewBox="0 0 12 12"><circle cx="6" cy="6" r="6" fill="var(--green)"/><rect x="3" y="4" width="6" height="4.2" fill="none" stroke="#fff" stroke-width=".9"/><path d="M3 4l3 2.3L9 4" fill="none" stroke="#fff" stroke-width=".9"/></svg>
        office@ridgelinebuild.com
      </li>
    </ul>
  </div>

  <div class="feature-name">
    <span class="feature-square"></span>
    <span class="feature-text">Ridgeline<br>Construction</span>
  </div>
</section>

<section class="card card-back">
  <div class="back-pattern" role="img" aria-label="Repeating tonal green pattern of the company mark"></div>
  <div class="back-mark">
    <span class="back-square"></span>
    <span class="back-name">Ridgeline Construction</span>
  </div>
</section>

</body>
</html>
```